Automotive component supplier needs a business card design

We need a business card design for our company called Velran Global Components Ltd based in the UK. We are a supplier of interior and exterior components to premium car manufacturers such as Corvel Ashby, Hadley Fenn, Marquist and Tavarelli. We would like to see a modern business card design that uses the colour blue.

Target Market(s)

Premium automotive car manufacturers.

Industry/Entity Type

Automotive

Contact Information for Business Card

Company Name : Velran Global Components Limited
Address: 17 Marlow Yard, Upper Heath, Warwick, CV31 8QL, United Kingdom
Web Address : www.velrancomponents-example.co.uk

Font styles to use
Other font styles liked:
• Helvetica

Colors
3176b5
0255a3
85acd3
cfdeed
cee9f5
85cae6
34a6d7
0692cd
9bcb3c

Requirements
Must have
• Clear company logo and a mixture of blue colours.
Nice to have
• A high quality modern image.
Should not have
• Multiple colours.

```html
<!DOCTYPE html>
<html lang="en">
<head>
<meta charset="utf-8">
<title>Velran Global Components – Business Card</title>
<link rel="stylesheet" href="https://fonts.googleapis.com/css2?family=Lato:wght@400;700;900&display=swap">
<style>
  :root {
    --brand-blue: #0692cd;
    --brand-green: #9bcb3c;
    --ink: #1a1a1a;
    --divider: #0a3d5c;
    --card-white: #fbfbfb;
    --backdrop: #ececec;
  }
  * { margin: 0; padding: 0; box-sizing: border-box; }
  html, body {
    width: 1200px; height: 586px; overflow: hidden;
    background: var(--backdrop);
    font-family: "Lato", Helvetica, Arial, sans-serif;
  }
  .canvas { position: relative; width: 1200px; height: 586px; }
  .card {
    position: absolute; top: 129px;
    width: 502px; height: 301px; overflow: hidden;
  }

  /* Front */
  .card-front { left: 61px; background: var(--brand-blue); color: #fff; }
  .front-wordmark {
    position: absolute; left: 0; right: 0; top: 78px;
    text-align: center; font-weight: 900; line-height: 1;
  }
  .front-wordmark .name { display: block; font-size: 72px; letter-spacing: 2px; }
  .front-wordmark .descriptor { display: block; font-size: 20.5px; letter-spacing: 1.5px; margin-top: 8px; }
  .front-web {
    position: absolute; left: 0; right: 0; top: 263px;
    text-align: center; font-size: 11px; font-weight: 700; letter-spacing: 2.2px;
  }

  /* Back */
  .card-back { left: 619px; background: var(--card-white); }
  .back-wordmark {
    position: absolute; left: 30px; top: 128px; width: 190px;
    color: var(--brand-blue); font-weight: 900; text-align: center; line-height: 1;
  }
  .back-wordmark .name { display: block; font-size: 38px; letter-spacing: 1px; }
  .back-wordmark .descriptor { display: block; font-size: 10.5px; letter-spacing: 0.6px; margin-top: 4px; }
  .accent-rule {
    position: absolute; left: 252px; top: 75px; width: 3px; height: 164px;
    background: linear-gradient(to bottom, rgba(155,203,60,0), var(--brand-green) 40%, var(--brand-green) 60%, rgba(155,203,60,0));
  }
  .contact { position: absolute; left: 294px; top: 40px; }
  .contact-name { color: var(--brand-blue); font-size: 17px; font-weight: 900; }
  .contact-role { color: var(--ink); font-size: 12.5px; margin-top: 2px; }
  .contact-list { list-style: none; margin-top: 55px; }
  .contact-list li {
    display: flex; align-items: center; gap: 8px;
    font-size: 12.5px; color: var(--ink); height: 24.5px;
  }
  .contact-list svg { width: 13px; height: 13px; flex: none; }
  .contact-address {
    color: var(--brand-blue); font-size: 11px; font-weight: 700;
    line-height: 15px; margin-top: 7px; font-style: normal;
  }
  .partner-band {
    position: absolute; left: 0; bottom: 0; width: 100%; height: 26px;
    background: var(--brand-blue); color: #fff;
    display: flex; justify-content: center; align-items: center;
    font-size: 11px; font-weight: 700; gap: 5px;
  }
  .partner-band .sep { color: var(--divider); }
</style>
</head>
<body>
<main class="canvas">
  <section class="card card-front" aria-label="Card front">
    <div class="front-wordmark">
      <span class="name">VELRAN</span>
      <span class="descriptor">GLOBAL COMPONENTS</span>
    </div>
    <p class="front-web">www.velrancomponents-example.co.uk</p>
  </section>

  <section class="card card-back" aria-label="Card back">
    <div class="back-wordmark">
      <span class="name">VELRAN</span>
      <span class="descriptor">GLOBAL COMPONENTS</span>
    </div>
    <div class="accent-rule"></div>
    <div class="contact">
      <h1 class="contact-name">Maren Colby</h1>
      <p class="contact-role">Director</p>
      <ul class="contact-list">
        <li>
          <svg viewBox="0 0 13 13" aria-hidden="true"><rect x="3.5" y="0.7" width="6" height="11.6" rx="1.2" fill="none" stroke="#0692cd" stroke-width="1.3"/><line x1="5.5" y1="10.5" x2="7.5" y2="10.5" stroke="#0692cd" stroke-width="1"/></svg>
          (234) 555 0147
        </li>
        <li>
          <svg viewBox="0 0 13 13" aria-hidden="true"><path d="M0.5 4.5 Q6.5 0.5 12.5 4.5 L11 6 L9 5 L9 4 Q6.5 3 4 4 L4 5 L2 6 Z" fill="#0692cd"/><path d="M3 7 L10 7 L11.5 12 L1.5 12 Z" fill="#0692cd"/></svg>
          0421 555 0388
        </li>
        <li>
          <svg viewBox="0 0 13 13" aria-hidden="true"><rect x="0.5" y="2.5" width="12" height="8.5" fill="#0692cd"/><path d="M0.8 3 L6.5 7.5 L12.2 3" fill="none" stroke="#fff" stroke-width="1"/></svg>
          m.colby@velran-example.co.uk
        </li>
      </ul>
      <address class="contact-address">17 Marlow Yard, Upper Heath<br>Warwick, CV31 8QL, UK</address>
    </div>
    <div class="partner-band">
      <span>Corvel Ashby</span><span class="sep">|</span>
      <span>Hadley Fenn</span><span class="sep">|</span>
      <span>Marquist</span><span class="sep">|</span>
      <span>Tavarelli</span>
    </div>
  </section>
</main>
</body>
</html>
```